Social Media App Needs PPT Template

We need a PowerPoint template for a new social media company based in the DC area called "Bold Ledger." We provide an interactive digital platform for executives to share actionable advice. We would like to see designs that use our orange logo color as an accent, but are mainly grey, white, and black. The final design should communicate clean, chic, modern, and professional.

Target Market(s)

Executives

Industry/Entity Type

Information Technology

Font styles to use
Sans Serif

Colors
f78f20
fbe7d2
ffffff
000000
e8e8e8
757575

Requirements
Must have
• My project must have title page and many options for the body of the ppt (graphs, tables, etc). It also needs to be easy to modify. I must have someone who is experienced in creating powerpoint templates.
Nice to have
• It would be nice to have a very modern and clean design that includes the logo on every page, but still leaves a lot of room for the content of the slide
Should not have
• My design project should not look to busy.

```html
<!DOCTYPE html>
<html lang="en">
<head>
<meta charset="utf-8">
<title>Bold Ledger — Chart Slide</title>
<link href="https://fonts.googleapis.com/css2?family=Lato:wght@300;400;700&display=swap" rel="stylesheet">
<style>
  :root {
    --backdrop: #cbcbcb;
    --sidebar: #222b3a;
    --accent: #f39220;
    --series-grey: #6b6b6d;
    --paper: #ffffff;
    --text: #4a4a4a;
    --muted: #666666;
    --gridline: #9a9a9a;
  }
  * { margin: 0; padding: 0; box-sizing: border-box; }
  html, body {
    width: 1200px; height: 960px; overflow: hidden;
    background: var(--backdrop);
    font-family: "Lato", sans-serif;
  }
  .canvas { position: relative; width: 1200px; height: 960px; }
  .slide {
    position: absolute; left: 120px; top: 143px;
    width: 958px; height: 719px;
    background: var(--paper);
  }
  .sidebar {
    position: absolute; left: 0; top: 0;
    width: 170px; height: 100%;
    background: var(--sidebar);
  }
  .brand {
    position: absolute; left: 0; top: 100px; width: 170px;
    display: flex; flex-direction: column; align-items: center; gap: 10px;
  }
  .brand-dot { width: 14px; height: 14px; border-radius: 50%; background: var(--accent); }
  .brand-name {
    color: var(--paper); font-weight: 700; font-size: 24px;
    letter-spacing: 0.5px; text-align: center; line-height: 1.1;
  }
  .site-url {
    position: absolute; left: 20px; bottom: 22px;
    color: var(--paper); font-weight: 300; font-size: 18px;
  }
  .slide-title {
    position: absolute; left: 204px; top: 96px;
    color: var(--accent); font-weight: 400; font-size: 41px; line-height: 1.2;
  }
  .title-rule {
    position: absolute; left: 204px; top: 154px;
    width: 716px; height: 1px; background: var(--accent);
  }
  .chart { position: absolute; left: 0; top: 0; }
  .chart text { font-family: "Lato", sans-serif; fill: var(--muted); }
  .body-copy {
    position: absolute; left: 200px; top: 485px; width: 724px;
    color: var(--text); font-size: 15.3px; line-height: 21.8px;
    text-align: justify;
  }
  .footer-rule {
    position: absolute; left: 802px; top: 664px;
    width: 124px; height: 1px; background: var(--sidebar);
  }
  .page-number {
    position: absolute; right: 35px; top: 680px;
    color: var(--muted); font-size: 13px;
  }
</style>
</head>
<body>
<div class="canvas">
  <section class="slide">
    <aside class="sidebar">
      <div class="brand">
        <span class="brand-dot"></span>
        <span class="brand-name">Bold Ledger</span>
      </div>
      <span class="site-url">boldledger.com</span>
    </aside>

    <h1 class="slide-title">Title of the page</h1>
    <div class="title-rule"></div>

    <svg class="chart" width="958" height="719" viewBox="150 179 1198 899" aria-label="Bar chart of three series across three categories">
      <g stroke="var(--gridline)" stroke-width="1" stroke-dasharray="10 8">
        <line x1="445" y1="449" x2="1178" y2="449"/>
        <line x1="445" y1="500" x2="1178" y2="500"/>
        <line x1="445" y1="549" x2="1178" y2="549"/>
        <line x1="445" y1="599" x2="1178" y2="599"/>
        <line x1="445" y1="649" x2="1178" y2="649"/>
      </g>
      <g stroke="var(--gridline)" stroke-width="1">
        <line x1="433" y1="449" x2="433" y2="704"/>
        <line x1="428" y1="698" x2="1178" y2="698"/>
      </g>
      <g font-size="17" text-anchor="end">
        <text x="418" y="458">5</text>
        <text x="418" y="509">4</text>
        <text x="418" y="558">3</text>
        <text x="418" y="608">2</text>
        <text x="418" y="658">1</text>
        <text x="418" y="709">0</text>
      </g>
      <g>
        <rect x="476" y="485" width="49" height="213" fill="var(--accent)"/>
        <rect x="524" y="527" width="49" height="171" fill="var(--sidebar)"/>
        <rect x="573" y="502" width="49" height="196" fill="var(--series-grey)"/>
        <rect x="705" y="515" width="49" height="183" fill="var(--accent)"/>
        <rect x="754" y="482" width="49" height="216" fill="var(--sidebar)"/>
        <rect x="802" y="529" width="49" height="169" fill="var(--series-grey)"/>
        <rect x="926" y="543" width="49" height="155" fill="var(--accent)"/>
        <rect x="975" y="495" width="49" height="203" fill="var(--sidebar)"/>
        <rect x="1023" y="478" width="49" height="220" fill="var(--series-grey)"/>
      </g>
      <g font-size="18" text-anchor="middle">
        <text x="545" y="734">Category 1</text>
        <text x="774" y="734">Category 2</text>
        <text x="1003" y="734">Category 3</text>
      </g>
      <g font-size="18">
        <rect x="1225" y="432" width="10" height="10" fill="var(--accent)"/>
        <text x="1239" y="445">Series 1</text>
        <rect x="1225" y="456" width="10" height="10" fill="var(--sidebar)"/>
        <text x="1239" y="469">Series 2</text>
        <rect x="1225" y="481" width="10" height="10" fill="var(--series-grey)"/>
        <text x="1239" y="493">Series 3</text>
      </g>
    </svg>

    <p class="body-copy">Duis autem vel eum iriure dolor in hendrerit in vulputate velit esse molestie consequat, vel illum dolore eu feugiat nulla facilisis at vero eros et accumsan et iusto odio dignissim qui blandit praesent luptatum zzril delenit augue duis dolore te feugait nulla facilisi. Nam liber tempor cum soluta nobis eleifend option congue nihil imperdiet doming id quod mazim placerat facer possim assum.</p>

    <div class="footer-rule"></div>
    <span class="page-number">Page 3</span>
  </section>
</div>
</body>
</html>
```